Velundra Jobs portal

Velundra Jobs is a job portal connecting job seekers and companies offering part time jobs in the Mena region, starting in the UAE. We would like to see designs that use the color blue. We have attached images to give an idea what the website should look like. When a company posts a job the job seekers are not allowed to see which company has posted a job. There should also be a coinvex gateway. On the landing page we want a catching picture that we will send.

Target Market(s)

Students and promotional workers

Logo Text

Velundra Jobs

Coding

Coded - Design and coding required

Number of Pages Required

4 page

Font styles to use
Sans Serif

Colors
33a6d7
0692cd
85cae6

```html
<!DOCTYPE html>
<html lang="en">
<head>
<meta charset="utf-8">
<title>Velundra Jobs</title>
<link href="https://fonts.googleapis.com/css2?family=Roboto:wght@400;500;700&display=swap" rel="stylesheet">
<style>
:root{
  --blue:#0692cd;
  --blue-mid:#33a6d7;
  --blue-light:#85cae6;
  --nav-blue:#1f5fa8;
  --header-bg:#f2f3f5;
  --panel-bg:#ebeced;
  --line:#d9dadc;
  --text:#333;
  --muted:#8a8a8a;
  --icon:#c5c7ca;
  --white:#fff;
}
*{box-sizing:border-box;margin:0;padding:0}
html,body{width:1156px;height:1200px;overflow:hidden}
body{font-family:'Roboto',sans-serif;background:var(--white);color:var(--text)}
.page{position:relative;width:1170px;height:1215px;transform:scale(0.98803);transform-origin:0 0}

.site-header{position:absolute;left:0;top:0;width:1170px;height:172px;background:var(--header-bg)}
.brand{position:absolute;left:99px;top:70px;display:flex;align-items:center;gap:10px;font-size:24px;font-weight:500;color:var(--blue)}
.brand-mark{width:18px;height:18px;background:var(--blue);border-radius:50%}
.main-nav{position:absolute;left:536px;top:77px;display:flex;gap:34px}
.main-nav a{color:var(--nav-blue);font-size:14px;font-weight:500;text-decoration:none}
.icon-search{position:absolute;left:764px;top:71px}
.notify{position:absolute;left:822px;top:72px}
.notify-badge{position:absolute;left:13px;top:-9px;width:26px;height:26px;border-radius:50%;background:var(--blue);border:2px solid var(--white);color:var(--white);font-size:12px;display:flex;align-items:center;justify-content:center}
.avatar{position:absolute;left:886px;top:64px;width:46px;height:46px;border-radius:50%;background:radial-gradient(circle,#b89078,#6a4a3a);border:3px solid #ddd}
.btn-logout{position:absolute;left:963px;top:68px;width:106px;height:38px;background:var(--blue-mid);color:var(--white);font-size:13px;font-weight:700;display:flex;align-items:center;justify-content:center;gap:9px}

.categories{position:absolute;left:98px;top:213px;width:273px;height:614px;border:2px solid var(--line);list-style:none}
.categories li{height:50.8px;border-bottom:1px solid var(--line);display:flex;align-items:center;padding-left:22px;font-size:14px}
.categories li:last-child{border-bottom:none}
.categories .label{flex:1}
.categories .count{color:var(--blue);font-size:13px;width:49px}

.search-bar{position:absolute;left:396px;top:213px;display:flex}
.field{height:54px;width:251px;border:1px solid var(--line);display:flex;align-items:center;padding:0 14px;color:var(--muted);font-size:15px;gap:13px}
.field.select{margin-left:11px;justify-content:space-between;padding:0 14px 0 17px}
.btn-find{width:145px;height:52px;margin-left:16px;margin-top:1px;background:var(--blue);color:var(--white);font-size:17px;font-weight:700;display:flex;align-items:center;justify-content:center}

.jobs-panel{position:absolute;left:397px;top:298px;width:675px;height:432px;background:var(--panel-bg);padding:24px 0 0 19px}
.jobs-table{width:640px;border-collapse:collapse;background:var(--white);box-shadow:0 8px 12px rgba(0,0,0,.08);table-layout:fixed}
.jobs-table th{background:var(--blue-mid);color:var(--white);font-size:13px;height:48px;font-weight:700;border-right:1px solid #5fb9e0}
.jobs-table td{height:65.6px;font-size:15px;text-align:center;border-right:1px solid var(--line);border-top:1px solid #eee}
.jobs-table td:first-child{text-align:left;padding-left:24px}
.jobs-table th:last-child,.jobs-table td:last-child{border-right:none}
.btn-apply{display:inline-block;width:104px;height:34px;line-height:34px;background:var(--blue);color:var(--white);font-size:13px;font-weight:700}

.section-title{position:absolute;left:398px;top:771px;color:var(--blue-mid);font-size:16px;font-weight:700}
.carousel-arrows{position:absolute;left:1038px;top:772px}

.providers{position:absolute;left:400px;top:813px;width:672px;height:228px;border:2px solid var(--line);display:flex;gap:26px;padding:22px 0 0 16px}
.provider{width:194px;text-align:center}
.provider-photo{height:145px}
.provider-name{margin-top:15px;font-size:16px;font-weight:500;color:var(--muted)}

.site-footer{position:absolute;left:0;top:1076px;width:1170px;height:139px;background:var(--blue);color:var(--white)}
.follow{position:absolute;left:99px;top:38px;font-size:12px;font-weight:500}
.social{position:absolute;left:99px;top:69px;display:flex;gap:6px}
.social span{width:31px;height:31px;display:block}
.footer-links{position:absolute;left:793px;top:41px;font-size:13px;font-weight:400;word-spacing:1px}
.footer-links p+p{margin-top:18px}
</style>
</head>
<body>
<div class="page">
<header class="site-header">
  <div class="brand"><span class="brand-mark"></span>Velundra Jobs</div>
  <nav class="main-nav"><a href="#">ABOUT US</a><a href="#">CONTACT US</a></nav>
  <svg class="icon-search" width="32" height="32" viewBox="0 0 32 32"><circle cx="13" cy="13" r="10" fill="none" stroke="var(--icon)" stroke-width="4"/><line x1="20" y1="20" x2="29" y2="29" stroke="var(--icon)" stroke-width="5" stroke-linecap="round"/></svg>
  <div class="notify">
    <svg width="28" height="32" viewBox="0 0 28 32"><path d="M14 3c-6 0-9 5-9 10v7l-3 5h24l-3-5v-7c0-5-3-10-9-10z" fill="var(--icon)"/><circle cx="14" cy="28" r="3.5" fill="var(--icon)"/></svg>
    <span class="notify-badge">23</span>
  </div>
  <div class="avatar" role="img" aria-label="User profile photo"></div>
  <div class="btn-logout"><svg width="12" height="15" viewBox="0 0 12 15"><rect x="0" y="6" width="12" height="9" rx="1" fill="#fff"/><path d="M3 6V4a3 3 0 0 1 6 0" fill="none" stroke="#fff" stroke-width="2"/></svg>LOGOUT</div>
</header>

<ul class="categories">
  <li><span class="label">Information Technology</span><span class="count">(33)</span></li>
  <li><span class="label">INFOSEC</span><span class="count">(3)</span></li>
  <li><span class="label">Mobility, Wireless</span><span class="count">(45)</span></li>
  <li><span class="label">Velomesh</span><span class="count">(32)</span></li>
  <li><span class="label">Sales</span><span class="count">(89)</span></li>
  <li><span class="label">Service Provider</span><span class="count">(56)</span></li>
  <li><span class="label">Security</span><span class="count">(4)</span></li>
  <li><span class="label">Big Data</span><span class="count">(8)</span></li>
  <li><span class="label">Cloud</span><span class="count">(256)</span></li>
  <li><span class="label">Ciraxo Consulting Services</span><span class="count">(20)</span></li>
  <li><span class="label">Data Center</span><span class="count">(158)</span></li>
  <li><span class="label">Engineering - Hardware</span><span class="count">(3)</span></li>
</ul>

<div class="search-bar">
  <div class="field"><svg width="12" height="12" viewBox="0 0 12 12"><circle cx="5" cy="5" r="3.5" fill="none" stroke="#aaa" stroke-width="1.6"/><line x1="7.5" y1="7.5" x2="11" y2="11" stroke="#aaa" stroke-width="1.6"/></svg>Keyword</div>
  <div class="field select">Select District<svg width="16" height="10" viewBox="0 0 16 10"><path d="M1 1l7 7 7-7" fill="none" stroke="#999" stroke-width="2.5"/></svg></div>
  <div class="btn-find">FIND JOB</div>
</div>

<section class="jobs-panel">
  <table class="jobs-table">
    <thead><tr><th style="width:230px">JOB TITLE</th><th style="width:114px">DUE DATE</th><th style="width:170px">PROVIDER NAME</th><th></th></tr></thead>
    <tbody>
      <tr><td>Information Technology</td><td>23 Jan 2015</td><td>Norvale</td><td><span class="btn-apply">APPLY NOW</span></td></tr>
      <tr><td>Engineering Hardware</td><td>02 Feb 2015</td><td>Tarrow Consultancy</td><td><span class="btn-apply">APPLY NOW</span></td></tr>
      <tr><td>Big Data</td><td>15 Mar 2015</td><td>BKR</td><td><span class="btn-apply">APPLY NOW</span></td></tr>
      <tr><td>Sales Manager</td><td>01 May 2015</td><td>Marlenda</td><td><span class="btn-apply">APPLY NOW</span></td></tr>
      <tr><td>Accounting</td><td>23 Jan 2015</td><td>Norvale</td><td><span class="btn-apply">APPLY NOW</span></td></tr>
    </tbody>
  </table>
</section>

<h2 class="section-title">FEATURED JOB PROVIDERS</h2>
<svg class="carousel-arrows" width="34" height="18" viewBox="0 0 34 18"><path d="M8 2L2 9l6 7" fill="none" stroke="#bbb" stroke-width="3"/><path d="M26 2l6 7-6 7" fill="none" stroke="var(--blue)" stroke-width="3"/></svg>

<div class="providers">
  <div class="provider"><div class="provider-photo" role="img" aria-label="Engineers in hard hats reviewing a laptop on site" style="background:linear-gradient(135deg,#6d6a64,#a9a59c)"></div><p class="provider-name">Management Service</p></div>
  <div class="provider"><div class="provider-photo" role="img" aria-label="Smiling accountant at a desk" style="background:linear-gradient(135deg,#e6eef6,#b9c9de)"></div><p class="provider-name">Accounting</p></div>
  <div class="provider"><div class="provider-photo" role="img" aria-label="Young man working at a computer in an office" style="background:linear-gradient(135deg,#c9b8a6,#8d8f93)"></div><p class="provider-name">Information Technology</p></div>
</div>

<footer class="site-footer">
  <p class="follow">FOLLOW US ON</p>
  <div class="social"><span style="background:#1c5da8"></span><span style="background:#17a6e3"></span><span style="background:#f0642a"></span></div>
  <div class="footer-links">
    <p>About Us &nbsp;|&nbsp; Terms and Conditions &nbsp;|&nbsp; Sitemap</p>
    <p>Copyrights @ 2015 All Rights Reserved</p>
  </div>
</footer>
</div>
</body>
</html>
```